Brindovalle Business cards

Dear team, I need to get the design file to suit it to our team. The focus of the business card is the Automotive Market and the design must be in black colour and the logo must be in glossy black. On the front of the card I need to get the following info:

- Name and Surname
- Title
- eMail
- Phone Number
- Skype account
- domain address

```html
<!DOCTYPE html>
<html lang="en">
<head>
<meta charset="UTF-8">
<title>Brindovalle Business Card</title>
<link href="https://fonts.googleapis.com/css2?family=Rubik:wght@400;500;700&display=swap" rel="stylesheet">
<style>
  :root {
    --backdrop: #0e0e0f;
    --card: #1c1c1e;
    --card-edge: #242427;
    --accent: #e8262c;
    --ink: #f4f4f4;
    --ink-soft: #d6d6d6;
  }
  html, body {
    margin: 0;
    width: 1200px;
    height: 900px;
    overflow: hidden;
    background: var(--backdrop);
    font-family: "Rubik", sans-serif;
  }
  .card {
    position: absolute;
    left: 150px;
    top: 193px;
    width: 900px;
    height: 514px;
    background: linear-gradient(160deg, var(--card-edge), var(--card) 45%);
    border-radius: 22px;
    box-shadow: 0 20px 50px rgba(0,0,0,0.6);
    overflow: hidden;
  }
  .brand {
    position: absolute;
    left: 70px;
    top: 62px;
    display: flex;
    align-items: center;
    gap: 16px;
  }
  .brand-mark {
    width: 38px;
    height: 38px;
    background: var(--accent);
  }
  .brand-name {
    font-size: 50px;
    font-weight: 700;
    color: var(--ink);
    letter-spacing: -0.5px;
  }
  .person {
    position: absolute;
    left: 0;
    top: 200px;
    padding-left: 70px;
  }
  .person-bar {
    position: absolute;
    left: 0;
    top: 4px;
    width: 34px;
    height: 42px;
    background: var(--accent);
  }
  .person-name {
    margin: 0;
    font-size: 40px;
    font-weight: 700;
    color: var(--accent);
    text-transform: uppercase;
    line-height: 1.1;
  }
  .person-title {
    margin: 4px 0 0;
    font-size: 22px;
    color: var(--ink-soft);
  }
  .contacts {
    position: absolute;
    left: 70px;
    top: 320px;
    margin: 0;
    padding: 0;
    list-style: none;
  }
  .contact-item {
    display: flex;
    align-items: center;
    gap: 12px;
    font-size: 22px;
    color: var(--ink);
    margin-bottom: 10px;
  }
  .contact-icon {
    width: 18px;
    height: 18px;
    flex: none;
  }
  .address {
    position: absolute;
    right: 60px;
    bottom: 48px;
    margin: 0;
    font-style: normal;
    text-align: right;
    font-size: 22px;
    line-height: 1.4;
    color: var(--ink);
  }
</style>
</head>
<body>
  <main class="card">
    <div class="brand">
      <span class="brand-mark"></span>
      <span class="brand-name">Brindovalle.com</span>
    </div>

    <section class="person">
      <span class="person-bar"></span>
      <h1 class="person-name">Marco Delvani</h1>
      <p class="person-title">Director</p>
    </section>

    <ul class="contacts">
      <li class="contact-item">
        <svg class="contact-icon" viewBox="0 0 24 24"><path fill="#e8262c" d="M6.6 10.8a15.1 15.1 0 0 0 6.6 6.6l2.2-2.2a1 1 0 0 1 1-.25 11.4 11.4 0 0 0 3.6.57 1 1 0 0 1 1 1V20a1 1 0 0 1-1 1A17 17 0 0 1 3 4a1 1 0 0 1 1-1h3.5a1 1 0 0 1 1 1c0 1.25.2 2.45.57 3.57a1 1 0 0 1-.25 1z"/></svg>
        555-014-2270
      </li>
      <li class="contact-item">
        <svg class="contact-icon" viewBox="0 0 24 24"><rect x="2" y="5" width="20" height="14" rx="2" fill="#e8262c"/><path d="M3 6l9 7 9-7" stroke="#1c1c1e" stroke-width="2" fill="none"/></svg>
        info@brindovalle.com
      </li>
      <li class="contact-item">
        <svg class="contact-icon" viewBox="0 0 24 24"><circle cx="12" cy="12" r="10" fill="#e8262c"/></svg>
        brindovalle
      </li>
    </ul>

    <address class="address">2740 W Harlan Ave, Corvel,<br>Nevada 89402</address>
  </main>
</body>
</html>
```